Heritage Hollow Business Cards

Require a business card design. <br/><br/>Needs to include logo (either round or long version) plus these details:<br/>Maya Torvell<br/>Heritage Hollow<br/>maya@kelvadtrading.com.au<br/>02 6481 7395<br/>PO Box Glenwarra NSW 2791<br/>www.heritagehollow.com.au<br/><br/>I need in an editable format so that I can create for multiple staff members. <br/><br/>

Target Market(s)

We are an online store selling renovation products to home owners are builders. Looking for a classic classy design.

Industry/Entity Type

Home And Garden

Contact Information for Business Card

Maya Torvell
Heritage Hollow
maya@kelvadtrading.com.au
02 6481 7395
PO Box Glenwarra NSW 2791
www.heritagehollow.com.au

Colors

Designer to choose colors to be used in the design.

Requirements
Must have
• Must include Logo.

```html
<!DOCTYPE html>
<html lang="en">
<head>
<meta charset="utf-8">
<title>Heritage Hollow Business Cards</title>
<link rel="stylesheet" href="https://fonts.googleapis.com/css2?family=Roboto+Slab:wght@400;700&family=Work+Sans:wght@400&display=swap">
<style>
  :root {
    --backdrop: #161616;
    --card: #222222;
    --card-edge: #2c2c2c;
    --silver: #cfcfcf;
    --silver-soft: #a9a9a9;
    --line: #8a8a8a;
  }
  * { box-sizing: border-box; margin: 0; padding: 0; }
  html, body { width: 1200px; height: 900px; overflow: hidden; }
  body {
    background: var(--backdrop);
    font-family: "Work Sans", sans-serif;
    color: var(--silver);
  }
  .sheet {
    position: relative;
    width: 1200px;
    height: 900px;
  }
  .card {
    position: absolute;
    left: 260px;
    width: 680px;
    height: 380px;
    background: var(--card);
    border: 1px solid var(--card-edge);
    box-shadow: 0 14px 30px rgba(0,0,0,0.55);
  }
  .card--front { top: 50px; }
  .card--back { top: 470px; }

  /* front */
  .front-brand {
    position: absolute;
    left: 0; right: 0; top: 0; bottom: 0;
    display: flex;
    align-items: center;
    justify-content: center;
    gap: 22px;
  }
  .brand-disc {
    width: 110px; height: 110px;
    border: 2px solid var(--silver-soft);
    border-radius: 50%;
  }
  .brand-name {
    font-family: "Roboto Slab", serif;
    font-weight: 400;
    font-size: 50px;
    color: var(--silver);
    letter-spacing: 0.5px;
  }

  /* back */
  .back-brand {
    position: absolute;
    left: 50px; top: 80px;
    width: 220px; height: 220px;
    border: 1.5px solid var(--silver-soft);
    border-radius: 50%;
    display: flex;
    align-items: center;
    justify-content: center;
    text-align: center;
  }
  .back-brand .brand-name { font-size: 32px; line-height: 1.05; }
  .divider {
    position: absolute;
    left: 318px; top: 70px;
    width: 1.5px; height: 240px;
    background: var(--line);
  }
  .contact {
    position: absolute;
    left: 350px; top: 78px;
  }
  .contact__name {
    font-family: "Roboto Slab", serif;
    font-weight: 700;
    font-size: 34px;
    letter-spacing: 3px;
    text-transform: uppercase;
    color: var(--silver);
  }
  .contact__company {
    font-size: 19px;
    margin-top: 2px;
    letter-spacing: 0.5px;
  }
  .contact__address {
    font-size: 18px;
    line-height: 1.3;
    margin-top: 12px;
    color: var(--silver-soft);
    letter-spacing: 0.5px;
  }
  .contact__list { list-style: none; margin-top: 12px; }
  .contact__item {
    display: flex;
    align-items: center;
    gap: 10px;
    font-size: 18px;
    line-height: 1.55;
    letter-spacing: 0.5px;
  }
  .contact__item svg { width: 14px; height: 14px; flex: none; }
</style>
</head>
<body>
<main class="sheet">
  <section class="card card--front" aria-label="Card front">
    <div class="front-brand">
      <span class="brand-disc"></span>
      <span class="brand-name">Heritage Hollow</span>
    </div>
  </section>

  <section class="card card--back" aria-label="Card back">
    <div class="back-brand">
      <span class="brand-name">Heritage<br>Hollow</span>
    </div>
    <span class="divider"></span>
    <div class="contact">
      <h1 class="contact__name">Maya Torvell</h1>
      <p class="contact__company">Heritage Hollow</p>
      <p class="contact__address">PO Box Glenwarra<br>NSW 2791</p>
      <ul class="contact__list">
        <li class="contact__item">
          <svg viewBox="0 0 16 16" aria-hidden="true"><path d="M4 1.5l2.2 3-1.4 1.6c.8 1.9 2.3 3.4 4.2 4.2l1.6-1.4 3 2.2-1.2 2.6C7.2 14 2 8.8 1.4 2.7z" fill="none" stroke="#cfcfcf" stroke-width="1.3"/></svg>
          02 6481 7395
        </li>
        <li class="contact__item">
          <svg viewBox="0 0 16 16" aria-hidden="true"><rect x="1.5" y="3.5" width="13" height="9" fill="none" stroke="#cfcfcf" stroke-width="1.3"/><path d="M1.5 3.5L8 9l6.5-5.5" fill="none" stroke="#cfcfcf" stroke-width="1.3"/></svg>
          maya@kelvadtrading.com.au
        </li>
        <li class="contact__item">
          <svg viewBox="0 0 16 16" aria-hidden="true"><circle cx="8" cy="8" r="6.5" fill="none" stroke="#cfcfcf" stroke-width="1.3"/><ellipse cx="8" cy="8" rx="2.8" ry="6.5" fill="none" stroke="#cfcfcf" stroke-width="1.1"/><path d="M1.5 8h13" stroke="#cfcfcf" stroke-width="1.1"/></svg>
          www.heritagehollow.com.au
        </li>
      </ul>
    </div>
  </section>
</main>
</body>
</html>
```